Card Design for my dog training business Brightpaw Obedience

Need a business card design for my dog training business with my new logo. Want the card to come off professional yet fun. Want it to be very eye catchy as well. I normally have these at vet clinics, pet stores, and groomers. so need it to look better than my competitors.
Target Market(s)
dog owners
Industry/Entity Type
Dog Training
Contact Information for Business Card
needs logo, my name and info
Font styles to use
Serif
Colors
0255a3
ffffff
ec1f27
000000
333333
fbfbfb
Requirements
Must have
- Brightpaw Obedience
- Felix Orland
- 415 903 2276
- info@brightpawobedience.example
- www.brightpawobedience.example

```html
<!DOCTYPE html>
<html lang="en">
<head>
<meta charset="utf-8">
<title>Brightpaw Obedience – Business Card</title>
<link href="https://fonts.googleapis.com/css2?family=EB+Garamond:ital,wght@0,500;1,400&family=Open+Sans:wght@400;700&display=swap" rel="stylesheet">
<style>
  :root{
    --backdrop:#3b332e;
    --card:#1d1e20;
    --ink:#fbfbfb;
    --silver:#c9cacc;
    --rule:#8a8b8e;
  }
  *{box-sizing:border-box;margin:0;padding:0}
  html,body{width:1200px;height:864px;overflow:hidden}
  body{background:var(--backdrop);position:relative;font-family:"Open Sans",sans-serif}
  .card{
    position:absolute;top:276px;width:540px;height:312px;
    background:var(--card);border-radius:4px;
    box-shadow:0 14px 30px rgba(0,0,0,.45);
    overflow:hidden;
  }
  .card--front{left:40px}
  .card--back{left:620px}

  .brand{display:flex;align-items:center;gap:10px;color:var(--silver);
    font-family:"EB Garamond",serif;font-weight:500;letter-spacing:.06em;white-space:nowrap}
  .brand__mark{width:12px;height:12px;background:var(--silver);flex:none}
  .card--front .brand{position:absolute;top:112px;left:0;right:0;justify-content:center;font-size:30px}
  .tagline{position:absolute;left:38px;bottom:40px;color:var(--silver);
    font-family:"EB Garamond",serif;font-style:italic;font-size:17px;white-space:nowrap}

  .card--back .brand{position:absolute;left:34px;top:138px;width:206px;font-size:19px;color:var(--ink);gap:8px}
  .card--back .brand__mark{background:var(--ink);width:10px;height:10px}
  .divider{position:absolute;left:256px;top:74px;width:1px;height:170px;background:var(--rule)}
  .contact{position:absolute;left:278px;top:106px;right:14px;color:var(--ink)}
  .contact__name{font-weight:700;font-size:22px;margin-bottom:10px}
  .contact__list{list-style:none;font-size:13.5px;line-height:22px}
  .contact__list li{display:flex;align-items:center;gap:8px;white-space:nowrap}
  .contact__list svg{width:13px;height:13px;flex:none}
</style>
</head>
<body>
  <section class="card card--front">
    <div class="brand"><span class="brand__mark"></span>Brightpaw Obedience</div>
    <p class="tagline">“Good manners start here, one happy dog at a time.”</p>
  </section>

  <section class="card card--back">
    <div class="brand"><span class="brand__mark"></span>Brightpaw Obedience</div>
    <div class="divider"></div>
    <div class="contact">
      <h1 class="contact__name">Felix Orland</h1>
      <ul class="contact__list">
        <li><svg viewBox="0 0 16 16" fill="#fbfbfb"><path d="M3 2h3l1.5 3.5-2 1.3a8 8 0 0 0 3.7 3.7l1.3-2L14 10v3a1 1 0 0 1-1 1A11 11 0 0 1 2 3a1 1 0 0 1 1-1z"/></svg>415 903 2276</li>
        <li><svg viewBox="0 0 16 16" fill="#fbfbfb"><path d="M1 3h14v10H1z"/><path d="M1 3l7 6 7-6" stroke="#1d1e20" stroke-width="1.4" fill="none"/></svg>info@brightpawobedience.example</li>
        <li><svg viewBox="0 0 16 16" fill="none" stroke="#fbfbfb" stroke-width="1.4"><circle cx="8" cy="8" r="6.3"/><ellipse cx="8" cy="8" rx="2.6" ry="6.3"/><path d="M1.7 8h12.6"/></svg>www.brightpawobedience.example</li>
      </ul>
    </div>
  </section>
</body>
</html>
```